Business Card

Just need business logo with phone number on it. 0487 312 654
And the following on the bottom of the card.

"Your local plumbing experts".
and emblems for zelpa card, cheque and cash

```html
<!DOCTYPE html>
<html lang="en">
<head>
<meta charset="utf-8">
<title>Ridgeway Plumbing &amp; Drainage — Business Card</title>
<link rel="stylesheet" href="https://fonts.googleapis.com/css2?family=Russo+One&family=Roboto+Condensed:wght@400;700&display=swap">
<style>
  :root {
    --page-bg: #e9ecef;
    --card-white: #ffffff;
    --brand-blue: #1aa6d6;
    --brand-blue-deep: #1488bd;
    --brand-blue-light: #2ec0e8;
    --brand-red: #e5303f;
    --ink-white: #ffffff;
    --icon-dark: #3b4650;
    --icon-green: #3fa34d;
  }
  * { box-sizing: border-box; margin: 0; padding: 0; }
  html, body {
    width: 1200px; height: 780px; overflow: hidden;
    background: var(--page-bg);
  }
  .canvas {
    position: relative; width: 1200px; height: 780px;
    display: flex; align-items: center; justify-content: center;
  }
  .card {
    position: relative; width: 1040px; height: 630px;
    background: var(--card-white);
    border-radius: 28px; overflow: hidden;
    box-shadow: 0 10px 30px rgba(0,0,0,0.18);
  }
  .card-panel { position: absolute; inset: 0; width: 100%; height: 100%; }

  .brand {
    position: absolute; left: 100px; top: 230px;
    font-family: "Russo One", sans-serif; font-weight: 400;
    color: var(--brand-red); text-transform: uppercase; line-height: 1;
  }
  .brand-initials { font-size: 76px; letter-spacing: 4px; display: block; }
  .brand-name { font-size: 44px; letter-spacing: 2px; display: block; margin-top: 10px; }
  .brand-trade { font-size: 20px; letter-spacing: 5px; display: block; margin-top: 10px; }

  .contact {
    position: absolute; left: 660px; top: 150px; width: 340px;
    color: var(--ink-white);
    font-family: "Roboto Condensed", sans-serif;
  }
  .phone { font-size: 48px; font-weight: 700; letter-spacing: 1px; white-space: nowrap; }
  .payments { display: flex; align-items: center; gap: 22px; margin-top: 24px; }
  .pay-card {
    display: flex; align-items: center; justify-content: center;
    width: 100px; height: 62px; border-radius: 6px;
    background: var(--card-white); box-shadow: 0 2px 4px rgba(0,0,0,0.25);
    font-family: "Roboto Condensed", sans-serif; font-weight: 700;
    font-size: 26px; color: var(--brand-blue-deep);
  }
  .pay-icon { width: 68px; height: 68px; display: block; }
  .tagline {
    margin-top: 30px; font-size: 27px; font-weight: 400; letter-spacing: 1px;
    white-space: nowrap;
  }
</style>
</head>
<body>
<main class="canvas">
  <section class="card" aria-label="Business card front">
    <svg class="card-panel" viewBox="0 0 1040 630" role="img" aria-label="Blue side panel where the red and blue wave decoration belongs">
      <defs>
        <linearGradient id="panelFill" x1="0" y1="0" x2="1" y2="1">
          <stop offset="0" stop-color="var(--brand-blue-light)"/>
          <stop offset="1" stop-color="var(--brand-blue-deep)"/>
        </linearGradient>
      </defs>
      <path d="M610 0 C570 200 540 420 460 630 L1040 630 L1040 0 Z" fill="url(#panelFill)"/>
    </svg>

    <h1 class="brand">
      <span class="brand-initials">RPD</span>
      <span class="brand-name">Ridgeway</span>
      <span class="brand-trade">Plumbing &amp; Drainage</span>
    </h1>

    <div class="contact">
      <p class="phone">0487 312 654</p>
      <div class="payments">
        <span class="pay-card">zelpa</span>
        <svg class="pay-icon cash-icon" viewBox="0 0 72 72" role="img" aria-label="Cash">
          <circle cx="36" cy="36" r="34" fill="var(--icon-dark)"/>
          <rect x="16" y="24" width="40" height="24" rx="3" fill="var(--icon-green)"/>
          <circle cx="36" cy="36" r="6" fill="var(--card-white)"/>
        </svg>
        <svg class="pay-icon cheque-icon" viewBox="0 0 72 72" role="img" aria-label="Cheque">
          <rect x="4" y="14" width="64" height="44" rx="6" fill="var(--card-white)" stroke="var(--icon-dark)" stroke-width="4"/>
          <line x1="14" y1="28" x2="58" y2="28" stroke="var(--icon-dark)" stroke-width="3"/>
          <line x1="14" y1="38" x2="46" y2="38" stroke="var(--icon-dark)" stroke-width="3"/>
          <line x1="14" y1="48" x2="36" y2="48" stroke="var(--brand-blue)" stroke-width="3"/>
        </svg>
      </div>
      <p class="tagline">Your local plumbing experts</p>
    </div>
  </section>
</main>
</body>
</html>
```